we can communicate on this, but i want to follow the approach we took on Pellew|Marsh & Quinlan but i feel the card front needs the black background and the platinum and gold logo. The back? I am open. we can use the same info from PM&Q. Velmont Arc is an enhanced equity investment fund - basically a very exclusive boutique hedge fund that uses only stock options. very advanced things. hope you are interested

Contact Information for Business Card

Dr. Lewis T. Brennick, CFA
Scientifique de fusée financière
701.555.0143
LTBquant47@mailvantor.com

4718 Willow Creek Bend W.
West Fargo, ND 58078

No web site

Colors

Designer to choose colors to be used in the design.

Requirements
Nice to have
• I tend to prefer the most visible applications of the logo to include logo and name, the logo version with a black background and the gold and platinum components separated by the black. I see this working well for a single side (logo and name - this is card front to me).
• I am fairly open to other treatments on the reverse side with the data. To me, it makes sense to have a different color rendition of the logo on the reverse and it may be a muted black tone on tone or an oversized portion that would have spot UV. Or, the reverse may play with colors and layout
Should not have
• Other colors = no no
• Decorative font

```html
<!DOCTYPE html>
<html lang="en">
<head>
<meta charset="UTF-8">
<title>Velmont Arc – Business Card</title>
<link href="https://fonts.googleapis.com/css2?family=Source+Sans+3:wght@400;600&display=swap" rel="stylesheet">
<style>
  :root {
    --backdrop: #d5d6d5;
    --card-black: #0d0d0d;
    --gold: #c9a227;
    --platinum: #e9e9e9;
    --muted: #a5a5a5;
    --rule: #6a6a6a;
  }
  * { box-sizing: border-box; margin: 0; padding: 0; }
  html, body { width: 1200px; height: 900px; overflow: hidden; }
  body {
    background: var(--backdrop);
    font-family: "Source Sans 3", "Myriad Pro", sans-serif;
    display: flex;
    align-items: center;
    justify-content: center;
    gap: 40px;
  }
  .card {
    position: relative;
    width: 540px;
    height: 310px;
    background: var(--card-black);
    overflow: hidden;
  }
  /* Front */
  .card-front {
    display: flex;
    align-items: center;
    justify-content: center;
    gap: 18px;
  }
  .brand-dot {
    width: 54px; height: 54px;
    border-radius: 50%;
    background: var(--gold);
  }
  .brand-name {
    color: var(--platinum);
    font-weight: 600;
    font-size: 44px;
    letter-spacing: 1px;
    text-transform: uppercase;
  }
  /* Back */
  .uv-circle {
    position: absolute;
    right: -90px;
    top: -150px;
    width: 360px;
    height: 360px;
    border-radius: 50%;
    background: radial-gradient(circle at 35% 70%, #2a2a2a 0%, #151515 45%, #050505 100%);
  }
  .contact {
    position: absolute;
    left: 36px;
    bottom: 32px;
    color: var(--muted);
    font-size: 13px;
    line-height: 1.45;
  }
  .person-name {
    color: var(--gold);
    font-weight: 600;
    font-size: 17px;
  }
  .person-name .credential { font-size: 13px; }
  .person-title { font-size: 13px; margin-bottom: 14px; }
  .divider { width: 40px; height: 1px; background: var(--rule); margin-bottom: 16px; }
  .address { margin-bottom: 4px; }
  .contact-line { display: flex; align-items: center; gap: 6px; }
  .contact-line svg { width: 11px; height: 11px; flex: none; }
</style>
</head>
<body>
  <section class="card card-front" aria-label="Card front">
    <span class="brand-dot"></span>
    <span class="brand-name">Velmont Arc</span>
  </section>

  <section class="card card-back" aria-label="Card back">
    <div class="uv-circle"></div>
    <div class="contact">
      <p class="person-name">Dr. Lewis T. Brennick, <span class="credential">CFA</span></p>
      <p class="person-title">Scientifique des Fusées Financières</p>
      <div class="divider"></div>
      <p class="address">4718 Willow Creek Bend W.<br>West Fargo, ND 58078</p>
      <p class="contact-line">
        <svg viewBox="0 0 12 12" fill="none" stroke="#c9a227" stroke-width="1.2"><rect x="3" y="0.8" width="6" height="10.4" rx="1"/></svg>
        701.555.0143
      </p>
      <p class="contact-line">
        <svg viewBox="0 0 12 12" fill="none" stroke="#c9a227" stroke-width="1.2"><rect x="0.8" y="2.5" width="10.4" height="7"/><path d="M0.8 2.5 6 7 11.2 2.5"/></svg>
        LTBquant47@mailvantor.com
      </p>
    </div>
  </section>
</body>
</html>
```